verdant terraces simple classy business card design

my name is colin barrow and I run a gardening business aimed at high class verdant terraces. the business name is verdant terraces and our logo was designed on pixel harbour .My clientel are anything from residential homes to businesses. I take pride in my work and know that I offer a service like no other in my area.
The business card will be used to represent my business and I want it to be not only rememberable, but simplistic and modern. Eye catching too. Of course I would like it relatable to gardening and appealing to the correct clientel - those being garden enthusiasts, prestigious homes and businesses that are after top of the line gardening services like no other on the market.
I am not a typical lawn mowing business so I don't want a typical card design that represents that. The gardens I work with are generally million dollar properties with owners who are very garden proud looking for upkeep and guidance from me along with sometimes whole new garden designs. I want the business cards to show to my clients that I take pride, as they do, in their garden. And I want them to know from my card that I am a professional, qualified horticulturist offering them a top of the line service for life. I want them to refer my business on. I want them to look at my business card and see class and professionalism in a modern unique bold way.
The card should be simple with the possibility of the logo on the front being embossed/debossed and my details on the back the card should have a organic garden feel it's very important to me that it is absolutely perfect
I am also very open to ideas and suggestions so look forward to seeing the designs. the business logo has been supplied with this project and I want the card to be double sided

Contact info is
Colin Barrow - Managing Director / Horticulturist
Phone : 0481 526 704
Email: colinbarrow@verdantterraces.example.au

Target Market(s)

high class gardens residential and commercial

Industry/Entity Type

Gardener

Contact Information for Business Card

Contact info is
Phone : 0481 526 704

PLEASE MAKE CARD DOUBLE SIDED

Requirements
Must have
• organic simple classy modern feel
• must flow with the current logo that has been supplied with this project
• Double sided
• Must explain in a simple way that I deal with high end gardens and I'm a qualified horticulturist
Nice to have
• embossed debossed logo
Should not have
• shouldn't be to busy or cheap looking

```html
<!DOCTYPE html>
<html lang="en">
<head>
<meta charset="utf-8">
<title>Verdant Terraces – Business Card</title>
<link rel="stylesheet" href="https://fonts.googleapis.com/css2?family=Arimo:wght@400;700&display=swap">
<style>
  :root {
    --backdrop: #ece7e1;
    --leaf-green: #4b8b3f;
    --brand-green: #3f8a3a;
    --paper: #fbfbf8;
    --ink: #2b2b2b;
    --ink-soft: #4a4a4a;
    --white: #ffffff;
  }
  * { box-sizing: border-box; margin: 0; padding: 0; }
  html, body {
    width: 1200px;
    height: 794px;
    overflow: hidden;
    background: var(--backdrop);
  }
  .canvas {
    position: relative;
    width: 1200px;
    height: 794px;
    display: flex;
    justify-content: center;
    align-items: center;
    gap: 80px;
  }
  .card {
    width: 340px;
    height: 595px;
    position: relative;
    box-shadow: 0 6px 18px rgba(0,0,0,0.12);
    font-family: "Arimo", sans-serif;
  }
  /* Front side */
  .card--front {
    background: var(--leaf-green);
    color: var(--white);
  }
  .front-mark {
    position: absolute;
    top: 150px;
    left: 0;
    right: 0;
    display: flex;
    flex-direction: column;
    align-items: center;
    gap: 22px;
  }
  .front-mark__circle {
    width: 150px;
    height: 150px;
    border-radius: 50%;
    background: var(--white);
  }
  .front-mark__name {
    font-weight: 700;
    font-size: 20px;
    letter-spacing: 0.08em;
    color: var(--white);
  }
  .front-web {
    position: absolute;
    bottom: 70px;
    left: 0;
    right: 0;
    text-align: center;
    font-size: 14px;
    letter-spacing: 0.03em;
    color: var(--white);
  }
  /* Back side */
  .card--back {
    background: var(--paper);
  }
  .brand {
    position: absolute;
    top: 80px;
    left: 0;
    right: 0;
    display: flex;
    justify-content: center;
    align-items: center;
    gap: 12px;
  }
  .brand__name {
    font-weight: 700;
    font-size: 22px;
    letter-spacing: 0.04em;
    color: var(--brand-green);
  }
  .brand__circle {
    width: 40px;
    height: 40px;
    border-radius: 50%;
    background: var(--brand-green);
  }
  .contact {
    position: absolute;
    top: 330px;
    left: 0;
    right: 0;
    text-align: center;
  }
  .contact__name {
    font-weight: 700;
    font-size: 19px;
    color: var(--brand-green);
    letter-spacing: 0.02em;
  }
  .contact__role {
    margin-top: 6px;
    font-size: 15px;
    color: var(--ink);
  }
  .contact__phone {
    margin-top: 18px;
    font-size: 15px;
    color: var(--brand-green);
  }
  .contact__line {
    margin-top: 6px;
    font-size: 13px;
    color: var(--ink-soft);
  }
</style>
</head>
<body>
  <main class="canvas">
    <section class="card card--front" aria-label="Card front">
      <div class="front-mark">
        <div class="front-mark__circle"></div>
        <div class="front-mark__name">VERDANT TERRACES</div>
      </div>
      <p class="front-web">www.verdantterraces.example.au</p>
    </section>

    <section class="card card--back" aria-label="Card back">
      <div class="brand">
        <span class="brand__name">VERDANT TERRACES</span>
        <div class="brand__circle"></div>
      </div>
      <div class="contact">
        <p class="contact__name">COLIN BARROW</p>
        <p class="contact__role">Managing Director / Horticulturist</p>
        <p class="contact__phone">P: 0481 526 704</p>
        <p class="contact__line">colinbarrow@verdantterraces.example.au</p>
        <p class="contact__line">verdantterraces.example.au</p>
      </div>
    </section>
  </main>
</body>
</html>
```